New Baby Formula Company Needs a Shopify Website Design

We are launching a baby formula company and need a Shopify website design. We have a patented product that is a disposable pouch with a frangible seal through the middle. The top half contains formula powder and the bottom half contains purified water. There is also a bottle nipple on the corner under the cap in order to feed the baby. You just need to squeeze the bottom half of the pouch to break the seal and then the water and formula will mix. You then only need to shake it and then remove the cap and feed the baby. We will also sell formula in containers like the other formula companies. We want this website to stand out and look professional. We don't want a boring layout, but something unique and captivating. I have attached a mockup rendering of our product, though it's not the finished product and our logo. This will let you know the color scheme we are going for. Let me know if you have any further questions. Thank you

```html
<!DOCTYPE html>
<html lang="en">
<head>
<meta charset="utf-8">
<title>MilaBloom – Baby Formula</title>
<link href="https://fonts.googleapis.com/css2?family=Cabin:wght@400;500;600;700&display=swap" rel="stylesheet">
<style>
:root{
  --green:#9fb236;
  --green-dark:#8a9c2a;
  --ink:#1c1c1c;
  --text:#333;
  --muted:#666;
  --tile:#f4f4f4;
  --footer:#272b2f;
  --white:#fff;
}
*{margin:0;padding:0;box-sizing:border-box}
html,body{width:1200px;height:3792px;overflow:hidden}
body{position:relative;font-family:'Cabin',sans-serif;color:var(--text);background:var(--white)}
.abs{position:absolute}
.btn{position:absolute;background:var(--green);color:var(--white);font-weight:600;font-size:14px;display:flex;align-items:center;justify-content:center;border-radius:4px}
.eyebrow{color:var(--green);font-size:21px;font-weight:500}
.heading{color:var(--ink);font-size:44px;font-weight:600}
.center{left:0;width:1200px;text-align:center}

/* top bar */
.topbar{top:0;left:0;width:1200px;height:46px;background:var(--green);color:var(--white);font-size:12px;font-weight:600}
.topbar .promo{left:111px;top:16px}
.topbar .meta{right:92px;top:18px;display:flex;gap:24px;font-size:13px}

/* header */
.header{top:46px;left:0;width:1200px;height:88px;background:var(--white)}
.logo{left:110px;top:12px;display:flex;align-items:center;gap:8px}
.logo .mark{width:22px;height:22px;border-radius:50%;background:var(--green)}
.logo .name{color:var(--green);font-weight:700;font-size:20px}
.nav{left:268px;top:42px;display:flex;gap:26px;font-size:13px;color:var(--ink)}
.nav .active{color:var(--green);text-decoration:underline}
.tools{left:810px;top:40px;display:flex;gap:40px;font-size:13px;color:var(--ink);align-items:center}
.tools span{display:flex;align-items:center;gap:7px}

/* hero */
.hero{top:134px;left:0;width:1200px;height:602px;background:linear-gradient(90deg,#f5f1ec 0%,#efe8e0 45%,#e6dbd0 100%);overflow:hidden}
.hero-photo{position:absolute;left:560px;top:0;width:640px;height:602px;background:radial-gradient(ellipse at 55% 45%,#c9b4a3 0%,#dcccbf 45%,#ebe2d9 80%)}
.hero .welcome{left:118px;top:115px;font-size:26px;color:var(--ink)}
.hero .brand{left:106px;top:170px;font-size:86px;font-weight:700;color:var(--green);letter-spacing:1px}
.hero .sub{left:110px;top:282px;font-size:38px;font-weight:600;color:var(--ink)}
.hero .btn{left:110px;top:358px;width:111px;height:35px;font-size:13px}
.pack{position:absolute;left:420px;top:420px;width:132px;height:182px;border-radius:8px 8px 14px 14px;background:linear-gradient(180deg,#f3f2e6 0%,#f3f2e6 45%,#a8ba42 46%,#94a833 100%)}

/* about */
.about-photo{left:128px;top:834px;width:384px;height:384px;border-radius:50%;background:radial-gradient(circle at 50% 45%,#9d948c 0%,#6e6a68 55%,#4b4e55 100%);border:10px solid var(--white);box-shadow:0 0 0 5px var(--green)}
.about .eyebrow{left:645px;top:818px}
.about .heading{left:645px;top:858px}
.about p{position:absolute;left:645px;top:922px;width:445px;font-size:12.5px;line-height:26px;color:var(--text)}
.checks{left:645px;top:1044px;width:450px;display:grid;grid-template-columns:240px 210px;row-gap:17px;font-size:12.5px;color:var(--ink)}
.checks span{display:flex;align-items:center;gap:16px}
.about .btn{left:645px;top:1178px;width:110px;height:37px}

/* offer cards */
.offer{top:1305px;width:482px;height:267px;border-radius:6px;overflow:hidden;box-shadow:0 4px 10px rgba(0,0,0,.2)}
.offer .photo{position:absolute;inset:0;background:linear-gradient(90deg,#3a3a3a 0%,#6d6d6a 35%,#b9b8b0 65%,#d9d7cf 100%)}
.offer .kicker{position:absolute;left:21px;top:58px;font-size:13px;font-weight:700;color:var(--white)}
.offer .save{position:absolute;left:21px;top:88px;font-size:22px;font-weight:700;color:var(--white);line-height:30px}
.offer .btn{left:25px;top:169px;width:109px;height:32px;font-size:13px}

/* products */
.products .eyebrow{top:1656px}
.products .heading{top:1697px}
.card{top:1799px;width:237px;height:273px;background:var(--tile)}
.card .thumb{position:absolute;left:52px;top:38px;width:132px;height:190px;border-radius:10px}
.thumb.pouch{background:linear-gradient(180deg,#f3f2e6 0%,#f3f2e6 48%,#a8ba42 49%,#94a833 100%)}
.thumb.tin{left:62px;top:55px;width:112px;height:160px;border-radius:12px;background:linear-gradient(90deg,#dcdcdc,#ffffff 50%,#dcdcdc)}
.thumb.tin.silver{background:linear-gradient(90deg,#8e8e8e,#e4e4e4 50%,#8e8e8e)}
.card-title{top:2090px;width:237px;text-align:center;font-size:17px;font-weight:600;color:var(--ink)}
.card-price{top:2119px;width:237px;text-align:center;font-size:14px}
.card-price s{color:var(--muted);margin-right:10px}
.card-price b{color:var(--green);font-weight:500}
.arrow{top:1953px;width:20px;height:20px;border-radius:50%;background:#e2e2e2;display:flex;align-items:center;justify-content:center}

/* sale */
.sale{top:2216px;left:0;width:1200px;height:500px;background:linear-gradient(90deg,#eef2f7 0%,#e3eaf2 50%,#d6e0ea 100%)}
.sale-photo{position:absolute;left:700px;top:30px;width:420px;height:440px;background:radial-gradient(ellipse at 50% 45%,#c9d4e2 0%,#d9e2ec 55%,rgba(217,226,236,0) 80%)}
.sale .eyebrow{left:110px;top:82px}
.sale .heading{left:108px;top:124px;line-height:54px;font-size:44px}
.count{top:260px;font-size:38px;color:var(--green)}
.count-label{top:304px;font-size:20px;color:var(--ink)}
.sale .btn{left:111px;top:361px;width:111px;height:37px}
.sale-pack{position:absolute;left:575px;top:222px;width:110px;height:170px;border-radius:8px;background:linear-gradient(180deg,#f3f2e6 0%,#f3f2e6 48%,#a8ba42 49%,#94a833 100%)}
.sale-tin{position:absolute;left:672px;top:262px;width:128px;height:168px;border-radius:14px;background:linear-gradient(90deg,#e0e0e0,#ffffff 50%,#e0e0e0)}

/* blog */
.blog .eyebrow{top:2779px}
.blog .heading{top:2813px}
.post{top:2900px;width:318px}
.post .img{width:318px;height:224px;border-radius:18px}
.post .date{position:absolute;left:2px;top:241px;width:62px;height:35px;background:var(--green);color:var(--white);font-size:13px;font-weight:600;border-radius:4px;display:flex;align-items:center;justify-content:center}
.post h3{position:absolute;left:83px;top:241px;font-size:17px;font-weight:600;color:var(--ink)}
.post p{position:absolute;left:83px;top:268px;width:230px;font-size:11px;line-height:18px;color:var(--text)}
.post .more{position:absolute;left:83px;top:315px;font-size:11px;color:var(--ink);display:flex;align-items:center;gap:8px}
.post .more i{width:18px;height:2px;background:var(--ink);display:block}
.blog .btn{left:545px;top:3264px;width:110px;height:37px}

/* footer */
.footer{top:3364px;left:0;width:1200px;height:428px}
.footer h4{position:absolute;top:131px;font-size:17px;font-weight:600;color:var(--white)}
.footer ul{position:absolute;top:178px;list-style:none;font-size:12.5px;color:var(--white);line-height:24px}
.contact{position:absolute;left:539px;top:174px;font-size:12.5px;color:var(--white)}
.contact div{display:flex;align-items:center;gap:20px;height:24px;margin-bottom:23px}
.newsletter{position:absolute;left:844px;top:174px;width:244px;height:34px;background:#eef0f4;border-radius:4px;font-size:12px;color:#333;display:flex;align-items:center;justify-content:space-between;padding:0 16px}
.rule{position:absolute;top:363px;height:1px;background:#8c8f93}
.social{position:absolute;left:540px;top:355px;display:flex;gap:25px}
.social i{display:block;width:12px;height:12px;border-radius:50%;background:#d7d9dc}
.copy{position:absolute;top:397px;width:1200px;text-align:center;font-size:12px;color:var(--white)}
</style>
</head>
<body>

<div class="abs topbar">
  <div class="abs promo">Get 10% off your next order using the coupon code "SAVE10" during checkout.</div>
  <div class="abs meta"><span>+1 555 010 2030</span><span>English</span><span>USD</span></div>
</div>

<header class="abs header">
  <div class="abs logo"><span class="mark"></span><span class="name">MilaBloom</span></div>
  <nav class="abs nav">
    <span class="active">Home</span><span>About Us</span><span>Shop</span><span>Pages</span><span>Blog</span><span>Look Book</span><span>More</span>
  </nav>
  <div class="abs tools">
    <span><svg width="18" height="18" viewBox="0 0 18 18" fill="none" stroke="#222" stroke-width="1.5"><circle cx="8" cy="8" r="6"/><path d="M12.5 12.5L17 17"/></svg>Search</span>
    <span><svg width="16" height="18" viewBox="0 0 16 18" fill="none" stroke="#222" stroke-width="1.5"><circle cx="8" cy="5" r="4"/><path d="M1 17c0-4 3-6 7-6s7 2 7 6"/></svg>Login</span>
    <span><svg width="16" height="18" viewBox="0 0 16 18" fill="none" stroke="#222" stroke-width="1.5"><path d="M2 5h12l-1 12H3z"/><path d="M5 5a3 3 0 0 1 6 0"/></svg>0 (items)</span>
  </div>
</header>

<section class="abs hero">
  <div class="hero-photo" role="img" aria-label="Mother smiling while feeding her baby from a bottle"></div>
  <div class="abs welcome">Welcome To</div>
  <div class="abs brand">MilaBloom</div>
  <div class="abs sub">Baby Formula</div>
  <div class="btn">Shop Now</div>
  <div class="pack" role="img" aria-label="Ready-to-mix formula pouch with purified water"></div>
  <svg class="abs" style="left:0;bottom:0" width="1200" height="60" viewBox="0 0 1200 60" preserveAspectRatio="none"><path d="M0 60V38C150 5 300 5 480 28S820 60 1000 40 1150 22 1200 30V60Z" fill="#fff"/></svg>
</section>

<section class="about">
  <div class="abs about-photo" role="img" aria-label="Mother in an armchair bottle-feeding her newborn"></div>
  <div class="abs eyebrow">About Us</div>
  <h2 class="abs heading">Who We Are?</h2>
  <p>Lorem ipsum dolor sit amet, consectetur adipiscing elit, sed do eiusmod tempor incididunt ut labore et dolore magna aliqua. Ut enim ad minim veniam, quis nostrud exercitation ullamco laboris nisi ut aliquip ex ea commodo consequat</p>
  <div class="abs checks">
    <span><svg width="19" height="19" viewBox="0 0 20 20" fill="none" stroke="#9fb236" stroke-width="1.5"><circle cx="10" cy="10" r="8.5"/><path d="M6 10h8M11 7l3 3-3 3"/></svg>Excepteur sint occaecat</span>
    <span><svg width="19" height="19" viewBox="0 0 20 20" fill="none" stroke="#9fb236" stroke-width="1.5"><circle cx="10" cy="10" r="8.5"/><path d="M6 10h8M11 7l3 3-3 3"/></svg>Occaecat cupidatat</span>
    <span><svg width="19" height="19" viewBox="0 0 20 20" fill="none" stroke="#9fb236" stroke-width="1.5"><circle cx="10" cy="10" r="8.5"/><path d="M6 10h8M11 7l3 3-3 3"/></svg>Sed ut perspiciatis</span>
    <span><svg width="19" height="19" viewBox="0 0 20 20" fill="none" stroke="#9fb236" stroke-width="1.5"><circle cx="10" cy="10" r="8.5"/><path d="M6 10h8M11 7l3 3-3 3"/></svg>Ut enim ad minima veniam</span>
    <span><svg width="19" height="19" viewBox="0 0 20 20" fill="none" stroke="#9fb236" stroke-width="1.5"><circle cx="10" cy="10" r="8.5"/><path d="M6 10h8M11 7l3 3-3 3"/></svg>Quis autem vel eum iur</span>
    <span><svg width="19" height="19" viewBox="0 0 20 20" fill="none" stroke="#9fb236" stroke-width="1.5"><circle cx="10" cy="10" r="8.5"/><path d="M6 10h8M11 7l3 3-3 3"/></svg>doloremque laudantium</span>
  </div>
  <div class="btn">Reda More</div>
</section>

<div class="abs offer" style="left:110px">
  <div class="photo" role="img" aria-label="Mother feeding her toddler a bottle by a window"></div>
  <div class="kicker">MILK BASED POWDER</div>
  <div class="save">SAVE<br>25 % OFF</div>
  <div class="btn">Shop Now</div>
</div>
<div class="abs offer" style="left:607px">
  <div class="photo" role="img" aria-label="Parents smiling at their baby at the kitchen table"></div>
  <div class="kicker">MILK BASED POWDER</div>
  <div class="save">SAVE<br>35 % OFF</div>
  <div class="btn">Shop Now</div>
</div>

<section class="products">
  <div class="abs eyebrow center">Products</div>
  <h2 class="abs heading center">Our Products</h2>
  <div class="abs arrow" style="left:33px"><svg width="10" height="10" viewBox="0 0 10 10" fill="none" stroke="#fff" stroke-width="1.5"><path d="M9 5H1M4 2L1 5l3 3"/></svg></div>
  <div class="abs arrow" style="left:1135px"><svg width="10" height="10" viewBox="0 0 10 10" fill="none" stroke="#fff" stroke-width="1.5"><path d="M1 5h8M6 2l3 3-3 3"/></svg></div>

  <div class="abs card" style="left:110px"><div class="thumb pouch" role="img" aria-label="Formula pouch"></div></div>
  <div class="abs card" style="left:356px"><div class="thumb tin" role="img" aria-label="White formula tin"></div></div>
  <div class="abs card" style="left:604px"><div class="thumb pouch" role="img" aria-label="Two formula pouches"></div></div>
  <div class="abs card" style="left:850px"><div class="thumb tin silver" role="img" aria-label="Silver formula tin"></div></div>

  <div class="abs card-title" style="left:110px">Lorem Ipsum Dolor Sit</div>
  <div class="abs card-title" style="left:356px">Lorem Ipsum Dolor Sit</div>
  <div class="abs card-title" style="left:604px">Lorem Ipsum Dolor Sit</div>
  <div class="abs card-title" style="left:850px">Lorem Ipsum Dolor Sit</div>
  <div class="abs card-price" style="left:110px"><s>$40.00</s><b>$40.00</b></div>
  <div class="abs card-price" style="left:356px"><s>$40.00</s><b>$40.00</b></div>
  <div class="abs card-price" style="left:604px"><s>$40.00</s><b>$40.00</b></div>
  <div class="abs card-price" style="left:850px"><s>$40.00</s><b>$40.00</b></div>
</section>

<section class="abs sale">
  <div class="sale-photo" role="img" aria-label="Baby sitting on a bed drinking from a bottle"></div>
  <svg class="abs" style="left:0;top:0" width="1200" height="40" viewBox="0 0 1200 40" preserveAspectRatio="none"><path d="M0 0H1200V10C1000 30 800 0 600 14S200 30 0 16Z" fill="#fff"/></svg>
  <svg class="abs" style="left:0;bottom:0" width="1200" height="40" viewBox="0 0 1200 40" preserveAspectRatio="none"><path d="M0 40H1200V28C1000 10 800 38 600 26S200 8 0 28Z" fill="#fff"/></svg>
  <div class="abs eyebrow">Offers</div>
  <h2 class="abs heading">50% Sale OFF We<br>Make Shopping Easy</h2>
  <div class="abs count" style="left:110px">-07</div>
  <div class="abs count" style="left:205px">-07</div>
  <div class="abs count" style="left:306px">-34</div>
  <div class="abs count" style="left:410px">-43</div>
  <div class="abs count-label" style="left:110px;top:298px">Days:</div>
  <div class="abs count-label" style="left:217px">Hours:</div>
  <div class="abs count-label" style="left:305px;top:298px">Minutes:</div>
  <div class="abs count-label" style="left:410px;top:298px">Seconds</div>
  <div class="btn">Shop Now</div>
  <div class="sale-pack" role="img" aria-label="Formula pouch"></div>
  <div class="sale-tin" role="img" aria-label="Formula tin"></div>
</section>

<section class="blog">
  <div class="abs eyebrow center">From The Blogs</div>
  <h2 class="abs heading center">Latest News</h2>

  <article class="abs post" style="left:110px">
    <div class="img" role="img" aria-label="Mother kissing her baby during a bottle feed" style="background:linear-gradient(135deg,#efe6da,#d8c8b8)"></div>
    <div class="date">July 02</div>
    <h3>Sed ut perspiciatis unde</h3>
    <p>Lorem ipsum dolor sit amet, consectetur adipiscing elit, sed do eiusmod tempor</p>
    <div class="more"><i></i>Read More</div>
  </article>
  <article class="abs post" style="left:440px">
    <div class="img" role="img" aria-label="Father bottle-feeding his baby" style="background:linear-gradient(135deg,#8a7566,#3d3c4a)"></div>
    <div class="date">July 03</div>
    <h3>Sed ut perspiciatis unde</h3>
    <p>Lorem ipsum dolor sit amet, consectetur adipiscing elit, sed do eiusmod tempor</p>
    <div class="more"><i></i>Read More</div>
  </article>
  <article class="abs post" style="left:770px">
    <div class="img" role="img" aria-label="Girl feeding a baby lying in bed" style="background:linear-gradient(135deg,#eef0f0,#d6d9dc)"></div>
    <div class="date">July 04</div>
    <h3>Sed ut perspiciatis unde</h3>
    <p>Lorem ipsum dolor sit amet, consectetur adipiscing elit, sed do eiusmod tempor</p>
    <div class="more"><i></i>Read More</div>
  </article>

  <div class="btn">View All</div>
</section>

<footer class="abs footer">
  <svg class="abs" style="left:0;top:0" width="1200" height="428" viewBox="0 0 1200 428" preserveAspectRatio="none"><path d="M0 18C250 60 420 60 600 22S950 -8 1200 26V428H0Z" fill="#272b2f"/></svg>
  <h4 style="left:110px">Quick Links</h4>
  <h4 style="left:308px">Help Links</h4>
  <h4 style="left:539px">Contact Info</h4>
  <h4 style="left:842px">Newsletter Sign up</h4>
  <ul style="left:112px"><li>Home</li><li>About Us</li><li>Shop</li><li>Pages</li><li>Blog</li><li>Look Book</li><li>More</li></ul>
  <ul style="left:309px"><li>Privacy Policy</li><li>Terms &amp; Conditions</li><li>Disclaimer</li><li>Faq</li><li>Shipping</li></ul>
  <div class="contact">
    <div><svg width="14" height="18" viewBox="0 0 14 18" fill="none" stroke="#fff" stroke-width="1.6"><path d="M7 17s6-6 6-10A6 6 0 0 0 1 7c0 4 6 10 6 10z"/><circle cx="7" cy="7" r="2"/></svg>Lorem Ipsum,Usa - 437916</div>
    <div><svg width="16" height="16" viewBox="0 0 16 16"><path d="M3 1l3 3-2 2c1 2 3 4 5 5l2-2 3 3-2 3C6 15 1 10 1 3z" fill="#fff"/></svg>+1 555 010 2030</div>
    <div><svg width="17" height="12" viewBox="0 0 17 12" fill="none" stroke="#fff" stroke-width="1.5"><rect x="1" y="1" width="15" height="10"/><path d="M1 1l7.5 6L16 1"/></svg>info@milabloom.com</div>
  </div>
  <div class="newsletter"><span>Your Email</span><svg width="12" height="10" viewBox="0 0 12 10" fill="none" stroke="#333" stroke-width="1.3"><path d="M1 5h10M7 1l4 4-4 4"/></svg></div>
  <div class="rule" style="left:110px;width:410px"></div>
  <div class="rule" style="left:715px;width:373px"></div>
  <div class="social"><i></i><i></i><i></i><i></i><i></i></div>
  <div class="copy">Copyright © 2024 &nbsp;MilaBloom .All rights Reserved</div>
</footer>

</body>
</html>
```